Etikett für Rotweinflasche
Liebe farbkosmos Atelier, wir werden uns bei der endgültigen Etikettengestaltung (finale Größe + Rückseite) noch an Euch melden. Bitte sendet uns euren Kontakt an helga.brandt@morvelli.wine
Zielgruppe
Morvelli Italia ist ein exklusives Boutique-Weingut in Sizilien, das hochqualitative Spitzenweine in kleinen Mengen mit modernster Technologie und stets nachhaltig erzeugt. Wir hinterfragen sowohl in der Agronomie im Weingarten als auch in der Önologie im Weinkeller alle herrschenden Traditionen und trachten danach, stets das beste Endprodukt zu kreieren. Der vulkanische, kalkreiche Boden Siziliens sowie trockene, sonnenreiche und niederschlagsarme Vegetationsperioden sind unsere optimale Basis.
Zielgruppe: Internationale Genussmenschen jeglichen Alters, die sich bewusst auch höherpreisige Weine (um die €30+) gönnen , vor allem kunstaffine young professionals mit Qualitäts-& Nachhaltigkeitsanspruch
Aufgabenstellung
Das Etikett ist für Rotwein-Flaschen (Cabernet Sauvignon / Nero D'Avola / Frappato / Syrah / Cerasuolo / Petit Verdot / sowie einen Bourdeaux-Cuveè aus Cabernet Sauvignon und Petit Verdot) .
Die Flasche ist reinschwarz, sehr hochwertig und schwer.
Flaschenform: Bordeauxflasche siehe technisches Datenblatt
Sleeve über dem Korken: schwarz mit weißer Schrift wie bisher
Zu gestalten ist das Etikett der Vorderseite. Zumindest die jeweilige Rotwein-Sorte ist auch textlich darzustellen (zwecks Scannen mit Trubel-App)
Der Kreativität kann freien Lauf gelassen werden! Unterscheidbarkeit vom Markt ist explizit gewollt.
Unsere aktuellen Etiketten und Markenauftritt siehe: https://morvelli.wine/shop/

```html
<!DOCTYPE html>
<html lang="de">
<head>
<meta charset="utf-8">
<title>Syrah – Etikett Vorderseite</title>
<link rel="stylesheet" href="https://fonts.googleapis.com/css2?family=Cormorant+Garamond:wght@500&display=swap">
<style>
  :root {
    --backdrop: #000000;
    --label-sky: #dcdbca;
    --label-haze: #cfcca4;
    --label-glow: #bdb461;
    --label-sea: #335d57;
    --label-foam: #9ba7a1;
    --label-mist: #8a8b87;
    --varietal-ink: #2b2f2a;
  }
  html, body {
    margin: 0;
    padding: 0;
    width: 1200px;
    height: 1187px;
    overflow: hidden;
    background: var(--backdrop);
  }
  .canvas {
    position: relative;
    width: 1200px;
    height: 1187px;
    background: var(--backdrop);
  }
  .front-label {
    position: absolute;
    left: 330px;
    top: 203px;
    width: 540px;
    height: 780px;
    overflow: hidden;
  }
  .label-artwork {
    position: absolute;
    inset: 0;
    width: 100%;
    height: 100%;
    display: block;
  }
  .varietal-name {
    position: absolute;
    top: 66px;
    left: 0;
    right: 0;
    margin: 0;
    text-align: center;
    font-family: "Cormorant Garamond", Georgia, serif;
    font-weight: 500;
    font-size: 30px;
    line-height: 1;
    letter-spacing: 0.6em;
    padding-left: 0.6em;
    color: var(--varietal-ink);
  }
</style>
</head>
<body>
<main class="canvas">
  <section class="front-label">
    <svg class="label-artwork" viewBox="0 0 540 780" preserveAspectRatio="none"
         role="img" aria-label="Surreale Meereslandschaft mit gelben Fischen in schwebenden Seifenblasen über türkisfarbener Brandung">
      <defs>
        <linearGradient id="artwork-tones" x1="0" y1="0" x2="0" y2="1">
          <stop offset="0" stop-color="var(--label-sky)"/>
          <stop offset="0.2" stop-color="var(--label-haze)"/>
          <stop offset="0.38" stop-color="var(--label-glow)"/>
          <stop offset="0.5" stop-color="var(--label-sea)"/>
          <stop offset="0.64" stop-color="var(--label-foam)"/>
          <stop offset="1" stop-color="var(--label-mist)"/>
        </linearGradient>
      </defs>
      <rect width="540" height="780" fill="url(#artwork-tones)"/>
    </svg>
    <h1 class="varietal-name">SYRAH</h1>
  </section>
</main>
</body>
</html>
```